Automotive Accessories Business Card

Design a business template that match our new logo design and our industry.

https://www.qelmotorgear.com/

Target Market(s)

Aftermarket auto parts and accessories

Industry/Entity Type

automotive

Contact Information for Business Card

company logo

Font styles to use
Serif
Sans Serif

Colors
EB3D1F
EC4F4E
F09395
F8D3D4
FCEDEE

```html
<!DOCTYPE html>
<html lang="en">
<head>
<meta charset="utf-8">
<title>QEL Motor Gear – Business Card</title>
<link href="https://fonts.googleapis.com/css2?family=Open+Sans:ital,wght@0,400;0,600;0,700;0,800;1,800&display=swap" rel="stylesheet">
<style>
  :root {
    --stage: #e9e7e4;
    --charcoal: #353535;
    --charcoal-deep: #2a2a2a;
    --charcoal-soft: #4a4a4a;
    --paper: #ffffff;
    --paper-shade: #efefef;
    --paper-shade-2: #e4e4e4;
    --red: #eb3d1f;
    --red-soft: #ec4f4e;
    --ink-light: #f2f2f2;
    --ink-muted: #c9c9c9;
  }
  * { box-sizing: border-box; margin: 0; padding: 0; }
  html, body {
    width: 1200px; height: 960px; overflow: hidden;
    background: var(--stage);
    font-family: "Open Sans", Arial, sans-serif;
  }
  .canvas {
    position: relative; width: 1200px; height: 960px;
    display: flex; flex-direction: column; align-items: center; justify-content: center; gap: 50px;
  }
  .card {
    position: relative; width: 700px; height: 400px; overflow: hidden;
    box-shadow: 0 6px 18px rgba(0,0,0,.18);
  }

  /* Front */
  .card--front { background: var(--charcoal); display: flex; }
  .front__brand {
    position: relative; width: 290px; height: 100%;
    background: var(--paper); overflow: hidden;
    display: flex; align-items: center; justify-content: center;
  }
  .front__facets { position: absolute; inset: 0; }
  .brand {
    position: relative; display: flex; align-items: center; gap: 10px;
    color: var(--charcoal); font-weight: 800; font-size: 26px; letter-spacing: .5px;
    line-height: 1;
  }
  .brand__mark { width: 14px; height: 14px; background: var(--red); flex: none; }
  .front__details {
    position: relative; flex: 1; padding: 80px 0 0 60px; color: var(--ink-light);
    background: linear-gradient(135deg, #3c3c3c 0%, var(--charcoal-deep) 100%);
  }
  .front__rule {
    position: absolute; left: 26px; top: 40px; bottom: 40px; width: 2px; background: var(--red);
  }
  .person__name { font-weight: 800; font-style: italic; font-size: 34px; letter-spacing: 1px; }
  .person__role { font-size: 18px; color: var(--ink-muted); margin-top: 2px; }
  .person__dash { width: 26px; height: 2px; background: var(--red); margin: 22px 0 22px; }
  .contact { list-style: none; display: flex; flex-direction: column; gap: 10px; font-size: 19px; }
  .contact__item { display: flex; align-items: center; gap: 12px; }
  .contact__icon { width: 20px; height: 20px; flex: none; fill: var(--ink-light); }
  .contact__web b { font-weight: 800; font-style: italic; }

  /* Back */
  .card--back { background: var(--charcoal); display: flex; align-items: center; justify-content: center; }
  .back__texture {
    position: absolute; inset: 0;
    background: radial-gradient(ellipse at 40% 45%, #5a5a5a 0%, var(--charcoal) 70%, var(--charcoal-deep) 100%);
  }
  .brand--reverse { color: var(--paper); font-size: 40px; gap: 14px; }
  .brand--reverse .brand__mark { width: 18px; height: 18px; }
</style>
</head>
<body>
<main class="canvas">
  <section class="card card--front">
    <div class="front__brand">
      <svg class="front__facets" viewBox="0 0 290 400" preserveAspectRatio="none" aria-hidden="true">
        <polygon points="0,0 290,0 290,120 60,400 0,400" fill="var(--paper-shade)"/>
        <polygon points="120,0 290,0 290,60 200,400 150,400" fill="var(--paper-shade-2)" opacity=".6"/>
        <polygon points="0,260 90,400 0,400" fill="var(--paper)"/>
      </svg>
      <div class="brand"><span class="brand__mark"></span>QEL MOTOR GEAR</div>
    </div>
    <div class="front__details">
      <span class="front__rule"></span>
      <h1 class="person__name">DANIEL ORTIZ</h1>
      <p class="person__role">Sales Manager</p>
      <div class="person__dash"></div>
      <ul class="contact">
        <li class="contact__item">
          <svg class="contact__icon" viewBox="0 0 24 24" aria-hidden="true"><path d="M6.6 10.8a15.1 15.1 0 0 0 6.6 6.6l2.2-2.2a1 1 0 0 1 1-.25 11.4 11.4 0 0 0 3.6.57 1 1 0 0 1 1 1V20a1 1 0 0 1-1 1A17 17 0 0 1 3 4a1 1 0 0 1 1-1h3.5a1 1 0 0 1 1 1c0 1.25.2 2.45.57 3.57a1 1 0 0 1-.25 1z"/></svg>
          1-866-555-0142
        </li>
        <li class="contact__item">
          <svg class="contact__icon" viewBox="0 0 24 24" aria-hidden="true"><path d="M2 5h20v14H2zm2 2v.5l8 5 8-5V7zm0 2.8V17h16V9.8l-8 5z"/></svg>
          sales@qelmotorgear.com
        </li>
        <li class="contact__item contact__web">
          <svg class="contact__icon" viewBox="0 0 24 24" aria-hidden="true"><path d="M12 2a10 10 0 1 0 0 20 10 10 0 0 0 0-20zm6.9 6h-2.9a15 15 0 0 0-1.4-3.6A8 8 0 0 1 18.9 8zM12 4c.8 1.2 1.5 2.5 1.9 4h-3.8c.4-1.5 1.1-2.8 1.9-4zM4.3 14a8 8 0 0 1 0-4h3.3a16 16 0 0 0 0 4zm.8 2h2.9c.3 1.3.8 2.5 1.4 3.6A8 8 0 0 1 5.1 16zM8 8H5.1a8 8 0 0 1 4.3-3.6C8.8 5.5 8.3 6.7 8 8zm4 12c-.8-1.2-1.5-2.5-1.9-4h3.8c-.4 1.5-1.1 2.8-1.9 4zm2.3-6H9.7a14 14 0 0 1 0-4h4.6a14 14 0 0 1 0 4zm.3 5.6c.6-1.1 1.1-2.3 1.4-3.6h2.9a8 8 0 0 1-4.3 3.6zm1.8-5.6a16 16 0 0 0 0-4h3.3a8 8 0 0 1 0 4z"/></svg>
          <span>www.<b>qelmotorgear</b>.com</span>
        </li>
      </ul>
    </div>
  </section>

  <section class="card card--back">
    <div class="back__texture" role="img" aria-label="Embossed dark grey square tile texture"></div>
    <div class="brand brand--reverse"><span class="brand__mark"></span>QEL MOTOR GEAR</div>
  </section>
</main>
</body>
</html>
```